Settlewell202.com flyer for window coverings

two sided 8 1/2 x 11 flyer featuring window coverings to send people to our website to shop for window coverings. Can use stock photos of blinds and shutters (wood toned blinds, white shutters, grey roller shades, white faux wood blinds). We don't sell draperies or drapery rods. We do sell other product like lighting and cabinet organization but we would like this flyer to focus on window coverings. We want to be a resource for new home buyers that need items to finish making their new house their home.

Target Market(s)

New home buyers

Industry/Entity Type

Real Estate

Font styles to use
Sans Serif

Requirements
Must have
• photos of window blinds and shades--photos have been added 3/31
• logo of settlewell202.com
• "Settlewell202.com - #1 - Cover your windows for: Privacy, Security, Energy Efficiency. We have all the styles to meet your needs and installation available!"
Should not have
• Pictures of towel bars

```html
<!DOCTYPE html>
<html lang="en">
<head>
<meta charset="utf-8">
<title>Settlewell202.com – Window Coverings Flyer</title>
<link href="https://fonts.googleapis.com/css2?family=Source+Sans+3:ital,wght@0,400;0,600;0,700;1,700&display=swap" rel="stylesheet">
<style>
  :root{
    --red:#d0212a;
    --ink:#1d1d1d;
    --grey-bg:#d7d8da;
    --paper:#ffffff;
    --ring:#e4e4e6;
    --gold:#ffe53b;
  }
  *{box-sizing:border-box;margin:0;padding:0}
  html,body{width:1200px;height:775px;overflow:hidden}
  body{background:var(--grey-bg);font-family:"Source Sans 3",Arial,sans-serif;color:var(--ink);position:relative}
  .page{position:absolute;top:55px;width:498px;height:647px;background:var(--paper);overflow:hidden;box-shadow:0 8px 14px rgba(0,0,0,.18)}
  .page--front{left:44px}
  .page--back{left:646px;background:linear-gradient(100deg,#f4f4f4 0%,#ffffff 35%,#ececec 60%,#f7f7f7 100%)}

  .brand{position:absolute;display:flex;align-items:center;gap:8px}
  .brand__mark{width:30px;height:30px;border-radius:50%;background:var(--red)}
  .brand__name{font-weight:700;font-size:26px;color:#3a3a3a;letter-spacing:.5px;line-height:1}
  .page--front .brand{left:36px;top:50px}
  .page--back .brand{left:36px;top:50px}

  .front-photo{position:absolute;left:385px;top:0;width:113px;height:647px;background:linear-gradient(90deg,#e9d3bd 0%,#c8996b 40%,#b98656 100%)}

  .headline{position:absolute;left:25px;top:167px;font-size:19px;font-weight:600;line-height:1.15}
  .headline .hi{color:var(--red)}
  .headline__site{display:block;font-weight:700;font-size:19px;color:var(--ink);margin-top:1px}
  .copy{position:absolute;left:25px;font-size:12px;line-height:1.45;width:370px}
  .copy .hi{color:var(--red);font-weight:600}
  .copy--cover{top:228px}
  .copy--shop{top:272px}
  .promo{color:var(--red);font-weight:700;font-style:italic}
  .promo b{font-size:15px}
  .phone{position:absolute;left:25px;top:335px;width:323px;height:54px;border-radius:14px;background:var(--red);color:#fff;font-size:25px;display:flex;align-items:center;justify-content:center;letter-spacing:.4px}
  .visit{position:absolute;left:25px;top:411px;font-size:10.5px;line-height:1.3}
  .visit__url{color:var(--red);font-weight:700;font-size:19px}

  .back-web{position:absolute;right:12px;top:9px;font-size:11px;color:var(--red)}
  .circles{position:absolute;left:0;top:0}
  .offer{position:absolute;left:22px;top:254px;width:176px;color:#fff;font-size:12.3px;line-height:1.28}
  .offer p+p{margin-top:14px}
  .offer .deal{color:var(--gold);font-weight:700}
  .gallery{position:absolute;left:310px;top:31px;width:190px;height:587px;border:2px solid var(--red);display:flex;flex-direction:column;gap:2px;background:var(--red)}
  .gallery__item{flex:1}
  .gallery__item--roller{background:linear-gradient(180deg,#e8e4d6,#cfc6b2 70%,#a7987c)}
  .gallery__item--shutter{background:linear-gradient(180deg,#c9c2bd,#b5aca6 70%,#6f6660)}
  .gallery__item--vertical{background:linear-gradient(90deg,#eceae4,#d9d6cd 60%,#b8ad8f)}
  .back-foot{position:absolute;left:22px;top:626px;font-size:10.5px}
  .back-foot a{color:var(--red);font-weight:700;text-decoration:none}
</style>
</head>
<body>

<section class="page page--front">
  <div class="front-photo" role="img" aria-label="Hand pulling the cord of wood-toned window blinds"></div>

  <div class="brand"><span class="brand__mark"></span><span class="brand__name">SETTLEWELL 202</span></div>

  <h1 class="headline"><span class="hi">Free Shipping</span> and <span class="hi">No Minimums!</span>
    <span class="headline__site">SETTLEWELL202.COM</span></h1>

  <p class="copy copy--cover">Cover your windows for: <span class="hi">Privacy, Security, Energy Efficiency.</span><br>We have all the styles to meet your needs and installation available!</p>

  <p class="copy copy--shop">Go to <span class="hi">www.settlewell202.com</span> to shop for your home and<br>during checkout enter your promo <span class="promo">code <b>SWL10</b></span> for your discount.</p>

  <div class="phone">Phone:&nbsp; 555-014-2290</div>

  <p class="visit">Visit us at: <span class="visit__url">www.settlewell202.com</span><br>Live chat available to answer any questions you might have.</p>
</section>

<section class="page page--back">
  <span class="back-web">www.settlewell202.com</span>

  <div class="brand"><span class="brand__mark"></span><span class="brand__name">SETTLEWELL 202</span></div>

  <svg class="circles" width="498" height="647" viewBox="0 0 498 647" aria-hidden="true">
    <circle cx="100" cy="369" r="205" fill="var(--ring)"/>
    <circle cx="90" cy="369" r="180" fill="var(--red)"/>
  </svg>

  <div class="offer">
    <p>Your builder and their supplier have PARTNERED together to offer you this special <span class="deal">10% discount</span> on a wide variety of window blinds and shades along with other products to finish making your house your home.</p>
    <p>We offer faux wood blinds, roller shades, verticals, faux wood shutters, sliding panels and honey comb shades in a variety of colors and finishes.</p>
  </div>

  <div class="gallery">
    <div class="gallery__item gallery__item--roller" role="img" aria-label="Kitchen window with a cream roller shade"></div>
    <div class="gallery__item gallery__item--shutter" role="img" aria-label="Arched window with white wood shutters"></div>
    <div class="gallery__item gallery__item--vertical" role="img" aria-label="Living room with white vertical blinds"></div>
  </div>

  <p class="back-foot">Visit us at: <a>www.settlewell202.com.</a>&nbsp; Live chat available to answer any questions you might have.</p>
</section>

</body>
</html>
```